Business card

We need a business card design for our company based in Auckland , New Zealand called 'Ridge + Studio Ltd'. We provide architectural services. We would like to see designs that use the max. three colours (such as white, black, grey) The final design should communicate financial safety and growth."
Also I will provide our company logo. I would like to the logo to be embeded onto our business card.

Target Market(s)

new residential house, alteration & addition & light commericila design & drafting service

Industry/Entity Type

Architecture

Contact Information for Business Card

Company name: ridge + studio Ltd.
Name: Mark Delford
Job title: architectural designer & Design LBP
email address: mark@rplusd.co.nz
mobile number: 02 5163 2290
web site: www.rplusd.co.nz

Requirements
Must have
• My project must have..
• - embeded logo (attached company logo)
• I don't have a bigger version for our company logo, but I have one old one, so you can remove the word from it)
• - insert the attached small BKTW logo & LBP logo
• - creative, simple and clear business card.
• - Max. three colours
Nice to have
• - Here are the samples I would like to share with you: http://www.plimvora.com/blog/minimalistic-business-card-designs/
• I would like to have my business card like one of the creation.
Should not have
• TBA

```html
<!DOCTYPE html>
<html lang="en">
<head>
<meta charset="utf-8">
<title>Ridge + Studio Ltd — Business Card</title>
<link rel="stylesheet" href="https://fonts.googleapis.com/css2?family=Source+Sans+3:wght@400;600;700&display=swap">
<style>
  :root {
    --backdrop: #3b3b3b;
    --ink: #000000;
    --paper: #ffffff;
    --mid-grey: #4a4a4a;
    --soft-grey: #7a7a7a;
    --line-grey: #b5b5b5;
  }
  * { box-sizing: border-box; margin: 0; padding: 0; }
  html, body {
    width: 1105px;
    height: 1200px;
    overflow: hidden;
    background: var(--backdrop);
    font-family: "Source Sans 3", "Myriad Pro", sans-serif;
  }
  .card {
    position: absolute;
    left: 193px;
    width: 718px;
    height: 410px;
    overflow: hidden;
  }
  .card--front { top: 166px; background: var(--ink); color: var(--paper); }
  .card--back { top: 622px; background: var(--paper); }

  .identity { position: absolute; left: 41px; top: 40px; }
  .identity__name {
    font-size: 24px;
    font-weight: 700;
    letter-spacing: 0.5px;
    line-height: 1.2;
  }
  .identity__role {
    font-size: 19px;
    font-weight: 400;
    line-height: 1.3;
    margin-top: 4px;
  }

  .contact { position: absolute; left: 41px; top: 258px; list-style: none; }
  .contact__item {
    display: flex;
    align-items: center;
    gap: 10px;
    font-size: 18px;
    line-height: 28px;
  }
  .contact__icon { width: 16px; height: 16px; flex: none; }
  .contact__company { font-size: 18px; margin-top: 8px; }

  .brand-disc { position: absolute; left: 258px; top: -22px; width: 456px; height: 456px; }
  .brand-disc__name {
    font-family: "Source Sans 3", "Myriad Pro", sans-serif;
    font-size: 34px;
    font-weight: 600;
    fill: var(--ink);
  }

  .credentials {
    position: absolute;
    left: 179px;
    top: 130px;
    display: flex;
    align-items: center;
    height: 153px;
  }
  .credentials__badge {
    width: 138px;
    height: 138px;
    border-radius: 50%;
    border: 10px solid var(--mid-grey);
    background: var(--paper);
  }
  .credentials__divider {
    width: 1px;
    height: 153px;
    background: var(--line-grey);
    margin: 0 18px 0 17px;
  }
  .credentials__member {
    font-size: 56px;
    font-weight: 700;
    color: var(--mid-grey);
    letter-spacing: -1px;
  }
  .back__web {
    position: absolute;
    left: 0;
    right: 0;
    top: 346px;
    text-align: center;
    font-size: 19px;
    color: var(--soft-grey);
  }
</style>
</head>
<body>
  <section class="card card--front">
    <div class="identity">
      <h1 class="identity__name">MARK DELFORD</h1>
      <p class="identity__role">architectural designer<br>&amp; Design LBP</p>
    </div>

    <ul class="contact">
      <li class="contact__item">
        <svg class="contact__icon" viewBox="0 0 16 16" aria-hidden="true">
          <rect x="4" y="0.5" width="8" height="15" rx="1.5" fill="none" stroke="#fff" stroke-width="1.5"/>
          <line x1="7" y1="13" x2="9" y2="13" stroke="#fff" stroke-width="1.2"/>
        </svg>
        02 5163 2290
      </li>
      <li class="contact__item">
        <svg class="contact__icon" viewBox="0 0 16 16" aria-hidden="true">
          <rect x="1" y="4" width="14" height="9" fill="#fff"/>
          <polyline points="1,4 8,9 15,4" fill="none" stroke="#000" stroke-width="1.2"/>
        </svg>
        mark@rplusd.co.nz
      </li>
      <li class="contact__item">
        <svg class="contact__icon" viewBox="0 0 16 16" aria-hidden="true">
          <circle cx="8" cy="8" r="7" fill="#fff"/>
          <path d="M4 6c1-1 3-1 3 1s-2 2-1 4M10 3c0 2 2 2 3 3M9 10c1 0 2 1 2 3" fill="none" stroke="#000" stroke-width="1.1"/>
        </svg>
        www.rplusd.co.nz
      </li>
      <li class="contact__company">ridge + studio Ltd.</li>
    </ul>

    <svg class="brand-disc" viewBox="0 0 456 456" role="img" aria-label="ridge + studio">
      <circle cx="228" cy="228" r="228" fill="#fff"/>
      <text class="brand-disc__name" x="228" y="240" text-anchor="middle">ridge + studio</text>
    </svg>
  </section>

  <section class="card card--back">
    <div class="credentials">
      <div class="credentials__badge" role="img" aria-label="Licensed practitioner badge"></div>
      <div class="credentials__divider"></div>
      <div class="credentials__member">BKTW</div>
    </div>
    <p class="back__web">www.rplusd.co.nz</p>
  </section>
</body>
</html>
```